Marlowe Group needs a business card

I would like the card to be simple but modern and elegant.
I like black and white.
or black and gold.
we are a private finance lender and also are involved in property and property developments.

please look at the business card photos i provided i would like M.G only one one side and all the other details on the other side use fonts that tie in with my theme.

Industry/Entity Type

Finance

Contact Information for Business Card

Marlowe Group (M.G) Daniel Marlowe M: 0413586207 E: danmarl@inboxmail.test

Font styles to use
Other font styles liked:
• Use fonts that would reflect our business

Colors
000000
ffffff

Requirements
Must have
• one side of details
• other side has either M.G or Marlowe Group like in the photos provided

```html
<!DOCTYPE html>
<html lang="en">
<head>
<meta charset="utf-8">
<title>Marlowe Group — Business Card</title>
<link rel="stylesheet" href="https://fonts.googleapis.com/css2?family=Cinzel:wght@400;700&family=Lato:wght@400&display=swap">
<style>
  :root {
    --page: #ffffff;
    --card: #000000;
    --gold: #f3c316;
    --gold-soft: rgba(243, 195, 22, 0.55);
    --white: #ffffff;
  }
  * { box-sizing: border-box; margin: 0; padding: 0; }
  html, body {
    width: 1200px;
    height: 900px;
    overflow: hidden;
    background: var(--page);
  }
  .canvas {
    position: relative;
    width: 1200px;
    height: 900px;
  }
  .card {
    position: absolute;
    top: 192px;
    height: 491px;
    background: var(--card);
    border-radius: 15px;
  }
  .card--front { left: 295px; width: 301px; }
  .card--back { left: 621px; width: 305px; }

  .top-rule {
    position: absolute;
    top: 48px;
    left: 70px;
    width: 176px;
    height: 1px;
    background: linear-gradient(90deg, transparent, rgba(243,195,22,0.15), transparent);
  }
  .monogram {
    position: absolute;
    left: 0;
    width: 100%;
    text-align: center;
    font-family: "Cinzel", serif;
    font-weight: 400;
    color: var(--gold);
    line-height: 1;
  }
  .card--front .monogram { top: 92px; font-size: 62px; }
  .card--back .monogram { top: 210px; font-size: 66px; }

  .company-name {
    position: absolute;
    top: 205px;
    left: 0;
    width: 100%;
    text-align: center;
    font-family: "Cinzel", serif;
    font-weight: 400;
    font-size: 22px;
    color: var(--gold);
    letter-spacing: 0.2px;
  }
  .person-name {
    position: absolute;
    top: 334px;
    left: 0;
    width: 100%;
    text-align: center;
    font-family: "Cinzel", serif;
    font-weight: 700;
    font-size: 17px;
    color: var(--gold);
    letter-spacing: 0.3px;
  }
  .name-rule {
    position: absolute;
    top: 364px;
    left: 55px;
    width: 190px;
    height: 1px;
    background: linear-gradient(90deg, transparent, var(--gold-soft), transparent);
  }
  .contact-list {
    position: absolute;
    top: 375px;
    left: 0;
    width: 100%;
    list-style: none;
    text-align: center;
    font-family: "Lato", sans-serif;
    font-size: 14px;
    line-height: 20px;
    color: var(--white);
  }
  .contact-label { color: var(--gold); }
</style>
</head>
<body>
  <main class="canvas">
    <section class="card card--front" aria-label="Card front with contact details">
      <div class="top-rule"></div>
      <div class="monogram">M.G</div>
      <h1 class="company-name">Marlowe Group</h1>
      <h2 class="person-name">DANIEL MARLOWE</h2>
      <div class="name-rule"></div>
      <ul class="contact-list">
        <li><span class="contact-label">M:</span> 0413586207</li>
        <li><span class="contact-label">E:</span> danmarl@inboxmail.test</li>
      </ul>
    </section>
    <section class="card card--back" aria-label="Card back with monogram">
      <div class="monogram">M.G</div>
    </section>
  </main>
</body>
</html>
```